Parcelwise HQ letterhead and envelope

Design a formal (8.5x11) letterhead and envelope for sales outreach and legal matters. Using design input from https://www.parcelwisehq.example/ and the attached documents.

Industry/Entity Type

Software Service

Requirements
Must have
• These 4 hex colors are our official colors:
• #355c98 [blue]
• #1eb1a2 [teal]
• #fdba12 [gold]
• #f1653b [orange]
• So no other colors besides these should be used.

```html
<!DOCTYPE html>
<html lang="en">
<head>
<meta charset="utf-8">
<title>Parcelwise HQ Letterhead</title>
<link rel="stylesheet" href="https://fonts.googleapis.com/css2?family=Lato:wght@400;700&family=Yellowtail&display=swap">
<style>
  :root {
    --brand-blue: #355c98;
    --brand-teal: #1eb1a2;
    --paper: #ffffff;
    --body-text: #555555;
    --ink: #222222;
    --rule: #9aa7bd;
  }
  * { margin: 0; padding: 0; box-sizing: border-box; }
  html, body { width: 996px; height: 1200px; overflow: hidden; background: var(--paper); }
  .letterhead {
    position: relative;
    width: 996px;
    height: 1200px;
    background: var(--paper);
    font-family: "Lato", Arial, sans-serif;
  }
  .brand-name {
    position: absolute;
    left: 52px;
    top: 36px;
    font-family: "Lato", Arial, sans-serif;
    font-weight: 400;
    font-size: 40px;
    line-height: 48px;
    color: var(--brand-blue);
    letter-spacing: 0.3px;
  }
  .address {
    position: absolute;
    left: 757px;
    top: 40px;
    padding-left: 14px;
    border-left: 1px solid var(--rule);
    font-family: Arial, Helvetica, sans-serif;
    font-size: 14.5px;
    line-height: 19px;
    color: var(--ink);
  }
  .address-line { display: flex; align-items: center; gap: 5px; }
  .address-line.indent { padding-left: 19px; }
  .address svg { width: 14px; height: 14px; flex: none; }
  .letter {
    position: absolute;
    left: 73px;
    top: 308px;
    width: 850px;
  }
  .salutation {
    font-weight: 700;
    font-size: 18px;
    color: var(--brand-blue);
    margin-bottom: 20px;
  }
  .letter p {
    font-size: 18px;
    line-height: 26px;
    color: var(--body-text);
    text-align: justify;
    hyphens: auto;
    margin-bottom: 17px;
  }
  .closing {
    margin-top: 34px;
    font-size: 21px;
    color: var(--ink);
  }
  .signature {
    font-family: "Yellowtail", cursive;
    font-size: 38px;
    line-height: 46px;
    color: var(--brand-blue);
    margin-top: 2px;
  }
  .footer-wave {
    position: absolute;
    left: 0;
    top: 1000px;
    width: 996px;
    height: 200px;
  }
  .footer-contacts {
    position: absolute;
    left: 0;
    top: 1170px;
    width: 996px;
    display: flex;
    justify-content: center;
    gap: 14px;
    font-family: Arial, Helvetica, sans-serif;
    font-size: 14.5px;
    color: #ffffff;
  }
  .contact { display: flex; align-items: center; gap: 5px; white-space: nowrap; }
  .contact svg { width: 14px; height: 14px; flex: none; }
</style>
</head>
<body>
<div class="letterhead">
  <header>
    <div class="brand-name">Parcelwise HQ</div>
    <div class="address">
      <div class="address-line">
        <svg viewBox="0 0 14 14" aria-hidden="true"><circle cx="7" cy="7" r="6" fill="none" stroke="#355c98" stroke-width="1.4"/><path d="M7 3.5a2.3 2.3 0 0 1 2.3 2.3C9.3 7.6 7 10.5 7 10.5S4.7 7.6 4.7 5.8A2.3 2.3 0 0 1 7 3.5z" fill="#355c98"/></svg>
        <span>482 Harbor Lane</span>
      </div>
      <div class="address-line indent">Fairview, MI 40012</div>
    </div>
  </header>

  <main class="letter">
    <div class="salutation">Dear Mr. Lorem,</div>
    <p>Lorem ipsum dolor sit amet, consectetuer adipiscing elit, sed diam nonummy nibh euismod tincidunt ut laoreet dolore magna aliquam erat volutpat. Ut wisi enim ad minim veniam, quis nostrud exerci tation ullamcorper suscipit lobortis nisl ut aliquip ex ea commodo consequat. Duis autem vel eum iriure dolor in hendiusto odio dignissim qui blandit praesent luptatum zzril delenit augue duis dolore te feugait nulla facilisi.</p>
    <p>Lorem ipsum dolor sit amet, consectetuer adipiscing elit, sed diam nonummy nibh euismod tincidunt ut laoreet dolore magna aliquam erat volutpat. Ut wisi enim ad minim veniam, quis nostrud exerci tation ullamcorper suscipit lobortis nisl ut aliquip ex ea commodo consequat. Duis autem vel eum iriure dolor in hendiusto odio dignissim qui blandit praesent luptatum zzril delenit augue duis dolore te feugait nulla facilisi.</p>
    <p>Lorem ipsum dolor sit amet, consectetuer adipiscing elit, sed diam nonummy nibh euismod tincidunt ut laoreet dolore magna aliquam erat volutpat. Ut wisi enim ad minim veniam, quis nostrud exerci tation ullamcorper suscipit lobortis nisl ut aliquip ex ea commodo consequat. Duis autem vel eum iriure dolor in hendiusto odio dignissim qui blandit praesent luptatum zzril delenit augue duis dolore te feugait nulla facilisi.</p>
    <div class="closing">Sincerely Your,</div>
    <div class="signature">Your Name</div>
  </main>

  <svg class="footer-wave" viewBox="0 0 996 200" aria-hidden="true">
    <path d="M0,50 C80,160 300,185 480,170 C680,152 820,100 996,88 L996,200 L0,200 Z" fill="#355c98"/>
    <path d="M0,36 C80,146 300,171 480,156 C680,138 820,86 996,74" fill="none" stroke="#ffffff" stroke-width="16"/>
    <path d="M0,36 C80,146 300,171 480,156 C680,138 820,86 996,74" fill="none" stroke="#1eb1a2" stroke-width="6"/>
    <path d="M0,20 C80,132 300,157 480,142 C680,124 820,72 996,60 L996,68 C820,80 680,132 480,150 C300,165 80,140 0,30 Z" fill="#355c98"/>
  </svg>

  <footer class="footer-contacts">
    <span class="contact">
      <svg viewBox="0 0 14 14" aria-hidden="true"><circle cx="7" cy="7" r="6" fill="none" stroke="#fff" stroke-width="1.2"/><rect x="5" y="3.5" width="4" height="7" rx="0.8" fill="none" stroke="#fff" stroke-width="1"/></svg>
      (678) 555-0142
    </span>
    <span class="contact">
      <svg viewBox="0 0 14 14" aria-hidden="true"><circle cx="7" cy="7" r="6" fill="none" stroke="#fff" stroke-width="1.2"/><path d="M4.5 4c.4 3 2.4 5.2 5.5 5.7l.5-1.4-1.5-.8-.7.6C7.3 7.6 6.6 6.9 6.2 5.9l.6-.7L6 3.7z" fill="#fff"/></svg>
      (877) 555-0190(Main)
    </span>
    <span class="contact">
      <svg viewBox="0 0 14 14" aria-hidden="true"><circle cx="7" cy="7" r="6" fill="none" stroke="#fff" stroke-width="1.2"/><rect x="3.8" y="5" width="6.4" height="4.4" fill="none" stroke="#fff" stroke-width="1"/><path d="M3.8 5l3.2 2.4L10.2 5" fill="none" stroke="#fff" stroke-width="1"/></svg>
      jsmith@parcelwisehq.example
    </span>
    <span class="contact">
      <svg viewBox="0 0 14 14" aria-hidden="true"><circle cx="7" cy="7" r="6" fill="none" stroke="#fff" stroke-width="1.2"/><ellipse cx="7" cy="7" rx="2.6" ry="6" fill="none" stroke="#fff" stroke-width="1"/><path d="M1 7h12" stroke="#fff" stroke-width="1"/></svg>
      www.parcelwisehq.example
    </span>
  </footer>
</div>
</body>
</html>
```